Create a wordpress website for Tovarin business solution

This project is to create a complete website with all pages.

Overview
The purpose of this project is to create a full complete website with all pages (16 pages). The site should be professional and modern. The site is for an IT recruiting and IT training company. The site needs to be easy to administer and update content. It should be simple to add pages, videos and testimonials later. I will leave the site layout, color schemes and flow to the designers.

Navigation Menu (Home, who we are, what we do, what makes us different, why it matters, candidate portal, contact us, Blog)

WHO WE ARE should be a drop down menu with link to pages (about us, mission, vision and purpose, our team)

WHAT WE DO should be drop down menu with link to the following pages (IT Recruiting, IT Training, Hardware and software sales)

What makes us different should be single page with different paragraph titles. (We live what we do, we don't compromise quality, we share knowledge, staffing guarantee)

Why it matters should be single page with paragraph titles. (Quickly fill positions, candidate career development)

Candidate portal should links to my portal login page. I can add the correct URL later. I just need it to link to somewhere. I can change it.

Contact us should have (address, phone number, google map and a form to submit request for a call back)

Blog - This link should launch a wordpress blogging module

Target Market(s)

IT RECRUITING AND CONSULTING

Industry/Entity Type

It Company

Coding

Coded - Design and coding required

Requirements
Must have
• Company Logo
• Navigation Menu (Home, who we are, what we do, what makes us different, why it matters, candidate portal, contact us)
• WHO WE ARE should be a drop down menu with link to pages (about us, mission, vision and purpose, our team)
• WHAT WE DO should be drop down menu with link to the following pages (IT Recruiting, IT Training, Hardware and software sales)
• What makes us different should be single page with different paragraph titles. (We live what we do, we don't compromise quality, we share knowledge, staffing guarantee)
• Why it matters should be single page with paragraph titles. (Quickly fill positions, candidate career development)
• Candidate portal should links to my portal login page. I can add the correct URL later. I just need it to link to somewhere. I can change it.
• Contact us should have (address, phone number, google map and a form to submit request for a call back)

```html
<!DOCTYPE html>
<html lang="en">
<head>
<meta charset="utf-8">
<title>Tovarin Business Solution LLC</title>
<link href="https://fonts.googleapis.com/css2?family=Montserrat:wght@300;400;500;600;700&family=Open+Sans:wght@400;600&display=swap" rel="stylesheet">
<style>
:root{
  --blue:#0b5aa8;
  --blue-deep:#064c92;
  --orange:#f08a1c;
  --orange-light:#f7a545;
  --brown:#8a4a06;
  --dark:#2b2d30;
  --ink:#222;
  --grey:#666;
  --panel:#f3f3f3;
  --white:#fff;
}
*{margin:0;padding:0;box-sizing:border-box}
html,body{width:1200px;height:3482px;overflow:hidden}
body{position:relative;font-family:"Open Sans",Arial,sans-serif;color:var(--ink);background:var(--white)}
.abs{position:absolute}
.heading{font-family:"Montserrat",Arial,sans-serif;font-weight:300;font-size:40px;text-align:center}
.heading b{font-weight:600}
.btn-outline{position:absolute;display:flex;align-items:center;justify-content:center;font-family:"Montserrat",Arial,sans-serif;font-size:14px;font-weight:600;border:2px solid var(--white);color:var(--white);border-radius:4px;text-decoration:none;letter-spacing:.5px}

/* nav */
.site-nav{top:0;left:0;width:1200px;height:65px;display:flex;justify-content:center;align-items:center;gap:14px;font-family:"Montserrat",Arial,sans-serif;font-size:15px;font-weight:500;color:#333;text-transform:uppercase;background:var(--white)}
.site-nav a{color:#333;text-decoration:none}
.site-nav a.active{color:var(--blue);font-weight:700}
.site-nav .sep{width:8px;height:8px;background:var(--orange);transform:rotate(45deg)}

/* hero */
.hero{top:65px;left:0;width:1200px;height:600px;background:linear-gradient(90deg,#c98a55 0%,#d9a577 40%,#9a7458 70%,#5d4b3e 100%)}
.hero-brand{top:135px;left:0;width:1200px;text-align:center;font-family:"Montserrat",Arial,sans-serif;font-weight:700;font-size:110px;color:var(--blue);line-height:1}
.hero-tagline{top:262px;left:0;width:1200px;text-align:center;font-family:"Montserrat",Arial,sans-serif;font-size:30px;font-weight:400;color:var(--white);letter-spacing:3px}
.hero-title{top:372px;left:0;width:1200px;text-align:center;font-family:"Montserrat",Arial,sans-serif;font-weight:500;font-size:78px;color:var(--white);letter-spacing:1px}
.hero-sub{top:465px;left:0;width:1200px;text-align:center;font-family:"Montserrat",Arial,sans-serif;font-size:29px;color:var(--white);letter-spacing:2px}
.hero-rule{top:486px;height:2px;width:170px;background:var(--orange)}
.btn-solid{position:absolute;top:550px;left:506px;width:206px;height:53px;background:var(--blue);color:var(--white);font-family:"Montserrat",Arial,sans-serif;font-size:16px;font-weight:600;display:flex;align-items:center;justify-content:center;border-radius:3px}

/* about */
.about{top:560px;left:0;width:1200px;height:512px}
.about-title{top:725px;left:80px;font-family:"Montserrat",Arial,sans-serif;font-weight:300;font-size:42px;color:var(--white)}
.about-title b{font-weight:700}
.about-text{top:788px;left:80px;width:640px;font-size:17px;line-height:26px;color:var(--white)}

/* services */
.service{position:absolute;top:1200px;width:340px;text-align:center}
.service .circle{width:172px;height:172px;border-radius:50%;margin:0 auto;border:8px solid #eee;display:flex;align-items:center;justify-content:center}
.service h3{margin-top:30px;font-family:"Montserrat",Arial,sans-serif;font-weight:600;font-size:24px;color:var(--blue)}
.service p{margin-top:12px;font-size:15px;line-height:23px;color:var(--grey)}
.btn-blue{position:absolute;display:flex;align-items:center;justify-content:center;border:2px solid var(--blue);color:var(--blue);font-family:"Montserrat",Arial,sans-serif;font-size:14px;font-weight:600;border-radius:4px}

/* testimonials */
.testimonials{top:1636px;left:0;width:1200px;height:416px;background:linear-gradient(90deg,#54585c 0%,#3d4145 50%,#25272a 100%)}
.quote-text{top:1830px;left:220px;width:760px;text-align:center;font-size:15px;line-height:24px;color:var(--white)}
.quote-mark{font-family:Georgia,serif;font-size:90px;color:rgba(255,255,255,.35);line-height:1}

/* different */
.diff-photo{top:2052px;left:0;width:469px;height:418px;background:linear-gradient(135deg,#9b7a66,#c9b7a8 50%,#6f6a66)}
.diff-panel{top:2052px;left:469px;width:731px;height:418px;background:var(--blue)}
.diff-title{top:2102px;left:529px;font-family:"Montserrat",Arial,sans-serif;font-weight:300;font-size:42px;color:var(--white)}
.diff-title b{font-weight:600}
.diff-text{top:2178px;left:529px;width:625px;font-size:16px;line-height:26px;color:var(--white)}

/* blog */
.blog-card{position:absolute;top:2595px;width:500px;height:209px;background:var(--panel);display:flex}
.blog-card .thumb{width:208px;height:209px}
.blog-card .body{padding:22px 24px}
.blog-card .date{font-size:14px;color:#444;display:flex;align-items:center;gap:8px}
.blog-card h4{margin-top:12px;font-family:"Montserrat",Arial,sans-serif;font-weight:500;font-size:19px;line-height:27px;color:var(--ink)}
.blog-card p{margin-top:10px;font-size:14px;line-height:22px;color:var(--grey)}

/* career */
.career{top:2855px;left:0;width:1200px;height:340px;background:linear-gradient(90deg,#4a4d50,#2f3134 60%,#1d1f21)}
.career-title{top:2900px;left:0;width:1200px;font-family:"Montserrat",Arial,sans-serif;font-weight:300;font-size:42px;text-align:center;color:var(--white)}
.career-title b{font-weight:600}
.phone-btn{top:2973px;left:364px;width:188px;height:51px;background:var(--blue);color:var(--white);font-family:"Montserrat",Arial,sans-serif;font-weight:600;font-size:18px;display:flex;align-items:center;justify-content:center;gap:12px;border-radius:3px}
.career-mail{top:2986px;left:585px;font-family:"Montserrat",Arial,sans-serif;font-size:17px;font-weight:500;color:var(--white)}
.career-mail a{color:var(--orange);text-decoration:underline}

/* contact */
.contact-title{top:3162px;left:0;width:1200px;font-family:"Montserrat",Arial,sans-serif;font-weight:300;font-size:42px;color:var(--white);text-align:center}
.contact-title b{font-weight:600}
.foot-brand{top:3232px;left:200px;width:320px;text-align:center;font-family:"Montserrat",Arial,sans-serif;font-weight:700;font-size:50px;color:var(--white);line-height:1}
.foot-tag{top:3286px;left:200px;width:320px;text-align:center;font-family:"Montserrat",Arial,sans-serif;font-size:13px;letter-spacing:2px;color:var(--white)}
.foot-text{top:3312px;left:60px;width:600px;text-align:center;font-size:14px;color:var(--white)}
.social{position:absolute;top:3350px;width:46px;height:46px;border-radius:50%;border:2px solid var(--white)}
.social.filled{background:var(--white)}
.contact-row{position:absolute;left:680px;display:flex;align-items:flex-start;gap:18px;color:var(--white);font-size:15px;line-height:25px}
.footer{top:3428px;left:0;width:1200px;height:54px;background:#1b1c1e;color:var(--white);font-family:"Montserrat",Arial,sans-serif;font-size:14px;display:flex;align-items:center;justify-content:center}
.footer span{color:var(--orange)}
</style>
</head>
<body>

<nav class="site-nav abs">
  <a class="active" href="#">Home</a><i class="sep"></i>
  <a href="#">Who We Are</a><i class="sep"></i>
  <a href="#">What We Do</a><i class="sep"></i>
  <a href="#">What Make Us Different</a><i class="sep"></i>
  <a href="#">Why It Matters</a><i class="sep"></i>
  <a href="#">Candidate Portal</a><i class="sep"></i>
  <a href="#">Contact Us</a>
</nav>

<!-- hero -->
<div class="hero abs" role="img" aria-label="Photo of a smiling team of young professionals gathered in an office"></div>
<div class="hero-brand abs">Tovarin</div>
<div class="hero-rule abs" style="top:280px;left:275px;width:70px"></div>
<div class="hero-tagline abs">BUSINESS SOLUTION LLC</div>
<div class="hero-rule abs" style="top:280px;left:855px;width:70px"></div>
<h1 class="hero-title abs">WE ARE RECRUITING</h1>
<div class="hero-rule abs" style="left:150px"></div>
<div class="hero-sub abs">Discover the Opportunity we offer</div>
<a class="btn-solid" href="#">CONTACT US NOW</a>

<!-- about band -->
<svg class="about abs" width="1200" height="512" viewBox="0 0 1200 512">
  <defs>
    <linearGradient id="aboutFade" x1="0" x2="1" y1="0" y2="0">
      <stop offset="0" stop-color="#0b5aa8"/>
      <stop offset=".55" stop-color="#0b5aa8"/>
      <stop offset=".75" stop-color="#0b5aa8" stop-opacity="0"/>
    </linearGradient>
    <linearGradient id="aboutPhoto" x1="0" x2="1" y1="0" y2="1">
      <stop offset="0" stop-color="#7d7a78"/>
      <stop offset=".5" stop-color="#b9b3ad"/>
      <stop offset="1" stop-color="#4f4a45"/>
    </linearGradient>
  </defs>
  <polygon points="0,55 1200,0 1200,512 0,512" fill="#0b5aa8"/>
  <rect role="img" aria-label="Photo of hands typing on a laptop beside a coffee cup" x="673" y="20" width="527" height="492" fill="url(#aboutPhoto)"/>
  <polygon points="0,55 1200,0 1200,512 0,512" fill="url(#aboutFade)"/>
  <polygon points="0,0 1200,0 1200,0 0,55" fill="none"/>
  <polygon points="980,10 1200,0 1200,70" fill="#2f3134"/>
</svg>
<h2 class="about-title abs">Know About <b>Tovarin</b></h2>
<p class="about-text abs">Lorem Ipsum is simply dummy text of the printing and typesetting industry. Lorem Ipsum has been the industry's standard dummy text ever since the 1500s, when an unknown printer took a galley of type and scrambled it to make a type specimen book. It has survived not only five centuries, but also the leap into electronic typesetting, remaining essentially unchanged.</p>
<a class="btn-outline" href="#" style="top:965px;left:77px;width:146px;height:52px">JOIN US NOW</a>

<!-- services -->
<h2 class="heading abs" style="top:1120px;left:0;width:1200px">Our <b>Services</b></h2>

<div class="service" style="left:74px">
  <div class="circle" style="background:var(--orange-light)">
    <svg width="84" height="84" viewBox="0 0 84 84" fill="none" stroke="#fff" stroke-width="5">
      <circle cx="36" cy="36" r="22"/><line x1="52" y1="52" x2="72" y2="72" stroke-linecap="round"/>
    </svg>
  </div>
  <h3>IT Recruiting</h3>
  <p>Lorem Ipsum is simply dummy text of the printing and typesetting industry. Lorem Ipsum has been the industry's standard dummy text ever.</p>
</div>
<div class="service" style="left:410px">
  <div class="circle" style="background:var(--orange)">
    <svg width="84" height="84" viewBox="0 0 84 84" fill="none" stroke="#fff" stroke-width="5">
      <rect x="14" y="12" width="56" height="38"/><line x1="42" y1="50" x2="28" y2="74"/><line x1="42" y1="50" x2="56" y2="74"/>
    </svg>
  </div>
  <h3>IT Training</h3>
  <p>Lorem Ipsum is simply dummy text of the printing and typesetting industry. Lorem Ipsum has been the industry's standard dummy text ever.</p>
</div>
<div class="service" style="left:786px">
  <div class="circle" style="background:var(--brown)">
    <svg width="84" height="84" viewBox="0 0 84 84" fill="none" stroke="#fff" stroke-width="5">
      <rect x="8" y="12" width="68" height="44" rx="3"/><line x1="42" y1="56" x2="42" y2="70"/><line x1="26" y1="72" x2="58" y2="72"/>
    </svg>
  </div>
  <h3>Hardware &amp; Software Sales</h3>
  <p>Lorem Ipsum is simply dummy text of the printing and typesetting industry. Lorem Ipsum has been the industry's standard dummy text ever.</p>
</div>
<a class="btn-blue" href="#" style="top:1532px;left:172px;width:144px;height:51px">READ MORE</a>
<a class="btn-blue" href="#" style="top:1532px;left:508px;width:144px;height:51px">READ MORE</a>
<a class="btn-blue" href="#" style="top:1532px;left:884px;width:144px;height:51px">READ MORE</a>

<!-- testimonials -->
<div class="testimonials abs" role="img" aria-label="Dimmed photo of a person working at a laptop"></div>
<h2 class="heading abs" style="top:1683px;left:0;width:1200px;color:var(--white)">What <b>Clients</b> Say</h2>
<div class="quote-mark abs" style="top:1758px;left:572px">&ldquo;</div>
<p class="quote-text abs">Lorem Ipsum is simply dummy text of the printing and typesetting industry. Lorem Ipsum has been the industry's standard dummy text ever since the 1500s, when an unknown printer took a galley of type and scrambled it to make a type specimen book.</p>
<div class="quote-mark abs" style="top:1900px;left:572px">&rdquo;</div>
<svg class="abs" style="top:1984px;left:556px" width="90" height="20" viewBox="0 0 90 20">
  <circle cx="12" cy="10" r="5" fill="none" stroke="#fff" stroke-width="1.5"/>
  <circle cx="45" cy="10" r="6" fill="#fff"/>
  <circle cx="78" cy="10" r="5" fill="none" stroke="#fff" stroke-width="1.5"/>
</svg>

<!-- different -->
<div class="diff-photo abs" role="img" aria-label="Photo of a cheerful team gathered around a laptop at a desk"></div>
<div class="diff-panel abs"></div>
<h2 class="diff-title abs">What Makes Us <b>Different</b></h2>
<p class="diff-text abs">Lorem Ipsum is simply dummy text of the printing and typesetting industry. Lorem Ipsum has been the industry's standard dummy text ever since the 1500s, when an unknown printer took a galley of type and scrambled it to make a type specimen book. It has survived not only five centuries, but also the leap into electronic typesetting, remaining essentially unchanged.</p>
<a class="btn-outline" href="#" style="top:2335px;left:529px;width:142px;height:51px">JOIN US NOW</a>

<!-- blog -->
<h2 class="heading abs" style="top:2517px;left:0;width:1200px">Latest <b>Blog</b></h2>
<article class="blog-card" style="left:77px">
  <div class="thumb" role="img" aria-label="Photo of a businessman looking through binoculars" style="background:linear-gradient(135deg,#cfd3d6,#8e9aa3)"></div>
  <div class="body">
    <div class="date"><svg width="14" height="14" viewBox="0 0 14 14"><rect x="1" y="2" width="12" height="11" fill="none" stroke="#555" stroke-width="1.5"/><line x1="1" y1="5" x2="13" y2="5" stroke="#555" stroke-width="1.5"/></svg>15 Feb 2016</div>
    <h4>LOREM IPSUM IS SIMPLY DUMMY</h4>
    <p>Lorem Ipsum is simply dummy text of the printing and typesetting industry.</p>
  </div>
</article>
<article class="blog-card" style="left:622px">
  <div class="thumb" role="img" aria-label="Photo of a smiling woman holding a tablet in an office" style="background:linear-gradient(135deg,#a8a19a,#5e5650)"></div>
  <div class="body">
    <div class="date"><svg width="14" height="14" viewBox="0 0 14 14"><rect x="1" y="2" width="12" height="11" fill="none" stroke="#555" stroke-width="1.5"/><line x1="1" y1="5" x2="13" y2="5" stroke="#555" stroke-width="1.5"/></svg>15 Feb 2016</div>
    <h4>LOREM IPSUM IS SIMPLY DUMMY</h4>
    <p>Lorem Ipsum is simply dummy text of the printing and typesetting industry.</p>
  </div>
</article>

<!-- career -->
<div class="career abs" role="img" aria-label="Dark photo of a laptop and phone on a desk"></div>
<h2 class="career-title abs">Contact Us for Your <b>Career</b></h2>
<div class="phone-btn abs">
  <svg width="20" height="20" viewBox="0 0 24 24" fill="#fff"><path d="M6.6 10.8a15.1 15.1 0 0 0 6.6 6.6l2.2-2.2c.3-.3.7-.4 1-.2 1.1.4 2.3.6 3.6.6.6 0 1 .4 1 1V20c0 .6-.4 1-1 1A17 17 0 0 1 3 4c0-.6.4-1 1-1h3.5c.6 0 1 .4 1 1 0 1.3.2 2.5.6 3.6.1.3 0 .7-.2 1z"/></svg>
  123-456-7890
</div>
<div class="career-mail abs">or mail us on our mail id <a href="#">here</a></div>

<!-- contact band -->
<svg class="abs" style="top:3060px;left:0" width="1200" height="368" viewBox="0 0 1200 368">
  <polygon points="0,60 1200,0 1200,368 0,368" fill="#0b5aa8"/>
  <polygon points="0,90 0,60 700,25" fill="#2f3134" opacity="0"/>
</svg>
<h2 class="contact-title abs">Contact <b>Us</b></h2>
<div class="foot-brand abs">Tovarin</div>
<div class="foot-tag abs">BUSINESS SOLUTION LLC</div>
<p class="foot-text abs">Lorem Ipsum is simply dummy text of the printing and typesetting</p>
<a class="social filled" href="#" style="left:242px" aria-label="Social profile"></a>
<a class="social" href="#" style="left:304px" aria-label="Social profile"></a>
<a class="social" href="#" style="left:367px" aria-label="Social profile"></a>

<div class="contact-row" style="top:3240px">
  <svg width="22" height="28" viewBox="0 0 22 28" fill="none" stroke="#fff" stroke-width="2"><path d="M11 27s9-10 9-16a9 9 0 0 0-18 0c0 6 9 16 9 16z"/><circle cx="11" cy="11" r="3"/></svg>
  <span>123, Building Name, Street NAme, Area, City,<br>Country - Zipcode</span>
</div>
<div class="contact-row" style="top:3306px">
  <svg width="22" height="22" viewBox="0 0 24 24" fill="none" stroke="#fff" stroke-width="2"><path d="M6.6 10.8a15.1 15.1 0 0 0 6.6 6.6l2.2-2.2c.3-.3.7-.4 1-.2 1.1.4 2.3.6 3.6.6.6 0 1 .4 1 1V20c0 .6-.4 1-1 1A17 17 0 0 1 3 4c0-.6.4-1 1-1h3.5c.6 0 1 .4 1 1 0 1.3.2 2.5.6 3.6.1.3 0 .7-.2 1z"/></svg>
  <span>123-4567-890</span>
</div>
<div class="contact-row" style="top:3356px">
  <svg width="24" height="18" viewBox="0 0 24 18" fill="none" stroke="#fff" stroke-width="2"><rect x="1" y="1" width="22" height="16"/><path d="M1 1l11 9 11-9"/></svg>
  <span>info@tovarinmail.com</span>
</div>

<footer class="footer abs">©&nbsp;<span>Tovarin</span>&nbsp;- 2016. All Rights Reserved.</footer>

</body>
</html>
```